Pop punk gig poster design!

In need of an amazing poster design for a gig We are organising, the genre is pop punk, and will be an all ages gig. I need to it bold, random and capture the eye of any bypasses, and make people want to go to the gig just because the poster is awesome! The event will be called "The great daydream" and will consist of three bands and an acoustic set to open. All the bands are full of energy and create an unreal ambiance during there shows, I would like to capture that in the poster. Open to anything spectacular, the sky is the limit.

• I need to have the name of the event "The Great Daydream"
Band names(in this order):
-Fold the Kite
-Velvet Tuesday
-Milo's Compass
-Tessaly Grovers

Date: Saturday 10th November 2012
Time: 5:15pm
Venue: The Quill, 74 Marrowby street, West End, QLD 4101
Ticket price: $10+bf online
$15 at the door.
Free BBQ

```html
<!DOCTYPE html>
<html lang="en">
<head>
<meta charset="utf-8">
<title>The Great Daydream – Gig Poster</title>
<link rel="stylesheet" href="https://fonts.googleapis.com/css2?family=Bangers&family=Special+Elite&display=swap">
<style>
  :root {
    --ink: #0d0d0b;
    --paper: #ffffff;
    --orange: #e2761c;
    --green: #6f9a1e;
    --yellow: #e9d21a;
    --olive: #3c3f14;
    --accent: #c8245a;
  }
  html, body {
    margin: 0;
    padding: 0;
    width: 800px;
    height: 1200px;
    overflow: hidden;
    background: var(--ink);
  }
  .poster {
    position: relative;
    width: 800px;
    height: 1200px;
    overflow: hidden;
  }
  .artwork {
    position: absolute;
    inset: 0;
    background:
      radial-gradient(ellipse 320px 260px at 620px 430px, rgba(233,210,26,0.85), transparent 70%),
      radial-gradient(ellipse 300px 300px at 180px 150px, rgba(226,118,28,0.8), transparent 70%),
      radial-gradient(ellipse 360px 300px at 250px 560px, rgba(111,154,30,0.9), transparent 70%),
      radial-gradient(ellipse 300px 260px at 640px 760px, rgba(226,118,28,0.75), transparent 70%),
      radial-gradient(ellipse 280px 240px at 130px 820px, rgba(60,63,20,0.9), transparent 70%),
      linear-gradient(180deg, #4a4418 0%, #6f8a1e 35%, #8a7a1a 60%, #3a2a10 85%, #1b1409 100%);
  }
  .artwork-shade {
    position: absolute;
    inset: 0;
    background: linear-gradient(180deg, transparent 60%, rgba(13,13,11,0.5) 78%, rgba(13,13,11,0.65) 100%);
  }
  .event-title {
    position: absolute;
    left: 400px;
    top: 390px;
    margin: 0;
    transform: translate(-50%, -50%) rotate(-48deg);
    white-space: nowrap;
    font-family: "Bangers", "Impact", sans-serif;
    font-weight: 400;
    font-size: 100px;
    letter-spacing: 2px;
    line-height: 1;
    color: var(--paper);
    -webkit-text-stroke: 3px var(--ink);
    paint-order: stroke fill;
    text-shadow: 4px 4px 0 var(--ink), -2px -2px 0 var(--ink);
  }
  .lineup {
    position: absolute;
    left: 0;
    width: 800px;
    margin: 0;
    display: flex;
    justify-content: center;
    gap: 22px;
    white-space: nowrap;
    font-family: "Bangers", "Impact", sans-serif;
    font-size: 46px;
    letter-spacing: 1px;
    color: var(--paper);
    -webkit-text-stroke: 2px var(--ink);
    paint-order: stroke fill;
    text-shadow: 3px 3px 0 var(--ink);
    line-height: 1;
  }
  .lineup-row-one { top: 885px; }
  .lineup-row-two { top: 952px; gap: 40px; }
  .lineup .label { color: var(--accent); }
  .details {
    position: absolute;
    top: 1028px;
    left: 0;
    width: 800px;
    margin: 0;
    text-align: center;
    font-family: "Special Elite", "Courier New", monospace;
    font-size: 17px;
    line-height: 31px;
    color: var(--paper);
    text-shadow: 1px 1px 2px var(--ink);
  }
  .details p { margin: 0; white-space: nowrap; }
</style>
</head>
<body>
  <main class="poster">
    <div class="artwork" role="img" aria-label="Abstract graffiti-style pattern of glossy black swirls and rings over orange, green and yellow"></div>
    <div class="artwork-shade"></div>

    <h1 class="event-title">The Great Daydream</h1>

    <p class="lineup lineup-row-one">
      <span class="label">Featuring</span><span class="band">Fold the Kite</span><span class="band">Velvet Tuesday</span>
    </p>
    <p class="lineup lineup-row-two">
      <span class="band">Milo's Compass</span><span class="band">Tessaly Grovers</span>
    </p>

    <section class="details">
      <p>SATURDAY 10th November 2012 - Time 5:15 PM</p>
      <p>Venue : The Quill , 74 Marrowby Street , West End QLD 4101</p>
      <p>Ticket Price $10 + Booking Fee online - $ 15 At The Door</p>
      <p>Free BBQ</p>
    </section>
  </main>
</body>
</html>
```